Southern Plantskills Academy needs a modern website that oozes professionalism

Our current website is boring and looks like everyone elses. We need a modern website that says we are the best at plant operator training. We use Brontovex and Hiraketo equipment for our training. We train all over Australia in Civil Construction, Mining and Quarrying. We want to be the "Go to" website for all plant operator training in Australia.

Industry/Entity Type

Heavy Machinery Training

Colors
0054AA
0677BA
7BADD7
CADEEF
E8F1F8
FFF300
FFF600
FEFA6F
FFFEC7
FFFEE8

```html
<!DOCTYPE html>
<html lang="en">
<head>
<meta charset="utf-8">
<title>Southern Plantskills Academy</title>
<link rel="stylesheet" href="https://fonts.googleapis.com/css2?family=Tinos:wght@400;700&family=Open+Sans:wght@400;600;700&display=swap">
<style>
:root{
  --navy:#1c3f74;
  --navy-deep:#163566;
  --heading:#1f4079;
  --yellow:#f9c80e;
  --red:#a5192d;
  --grey-bg:#efefef;
  --section-bg:#ebebeb;
  --text:#444;
  --footer:#22222f;
  --white:#fff;
}
*{margin:0;padding:0;box-sizing:border-box}
html,body{width:1200px;height:4889px;overflow:hidden}
body{position:relative;background:var(--white);font-family:"Open Sans",Arial,sans-serif;color:var(--text)}
.abs{position:absolute}
.serif{font-family:"Tinos","Times New Roman",serif}
.photo{position:absolute}
.eyebrow{position:absolute;font-size:8px;font-weight:700;letter-spacing:.3px;color:#222;text-transform:uppercase}
.section-title{position:absolute;font-family:"Tinos","Times New Roman",serif;font-weight:700;color:var(--heading);font-size:48px;line-height:59px;letter-spacing:1.2px}
.rule{position:absolute;height:2px;width:32px;background:var(--yellow)}
.body-copy{position:absolute;font-size:11px;line-height:17px;color:#555}
.btn{position:absolute;display:flex;align-items:center;justify-content:center;font-size:8px;font-weight:700;color:var(--white);text-transform:uppercase;letter-spacing:.3px}
.btn-yellow{background:var(--yellow)}
.btn-red{background:var(--red)}

/* hero */
.hero-bg{left:0;top:0;width:1016px;height:659px;background:var(--grey-bg)}
.nav a{position:absolute;top:38px;font-size:13px;color:#333;text-decoration:none;text-transform:uppercase}
.brand{left:156px;top:110px;display:flex;align-items:center;gap:10px}
.brand-mark{width:34px;height:34px;border-radius:50%;background:var(--yellow)}
.brand-name{font-family:"Open Sans",sans-serif;font-weight:700;font-size:13px;line-height:16px;color:var(--navy);letter-spacing:.4px;text-transform:uppercase}
.hero-title{left:142px;top:203px;font-family:"Tinos",serif;font-weight:700;font-size:60px;line-height:61px;color:var(--heading);letter-spacing:1.5px}

/* about */
.call-box{left:218px;top:1062px;width:365px;height:150px;background:var(--navy);color:var(--white)}
.call-label{left:118px;top:50px;font-size:15px;font-family:"Tinos",serif}
.call-number{left:118px;top:74px;font-size:27px;font-weight:700;font-family:"Tinos",serif;letter-spacing:.5px}

/* services */
.services-bg{left:0;top:1284px;width:1200px;height:727px;background:var(--section-bg)}
.card{position:absolute;top:1548px;width:317px;height:294px;background:var(--white)}
.card .photo{left:0;top:0;width:317px;height:191px}
.card-label{position:absolute;left:0;right:0;top:232px;text-align:center;font-family:"Tinos",serif;font-size:21px;color:#2a4e86;letter-spacing:.5px}

/* video */
.video{left:0;top:2011px;width:1200px;height:454px;background:linear-gradient(100deg,#3d2a26 0%,#2e2b30 40%,#34353e 70%,#2a3238 100%)}
.play{left:517px;top:2132px;width:160px;height:160px;border:2px solid rgba(255,255,255,.85);border-radius:50%}
.play-label{left:0;right:0;top:86px;text-align:center;font-size:14px;font-weight:600;color:var(--white)}
.video-title{left:0;width:1226px;top:2322px;text-align:center;font-family:"Tinos",serif;font-size:48px;color:var(--white);letter-spacing:1.5px}

/* banner */
.banner{left:0;top:3166px;width:1200px;height:493px;background:linear-gradient(110deg,#4d4b45 0%,#5e5a4f 40%,#4c4a47 70%,#3e3e42 100%)}
.banner-title{left:152px;top:3272px;font-family:"Tinos",serif;font-weight:700;font-size:58px;line-height:66px;color:var(--white);letter-spacing:1.5px}
.lower-bg{left:0;top:3659px;width:1200px;height:841px;background:var(--grey-bg)}
.quote{left:380px;top:3566px;width:661px;height:272px;background:var(--white);box-shadow:0 4px 18px rgba(0,0,0,.06)}
.quote-text{left:76px;top:63px;width:410px;font-family:"Tinos",serif;font-size:18px;line-height:25.5px;color:#444}

/* contact */
.field{position:absolute;background:var(--white);font-size:10px;color:#555;padding:14px 0 0 20px}
.email-box{left:239px;top:4237px;width:272px;height:108px;background:var(--navy);color:var(--white)}

/* footer */
.footer{left:0;top:4500px;width:1200px;height:389px;background:var(--footer);color:var(--white)}
.f-label{position:absolute;font-size:9px;color:#b9b9c4;text-transform:uppercase;letter-spacing:.3px}
.f-value{position:absolute;font-family:"Tinos",serif;font-size:17px;color:var(--white)}
.f-rule{position:absolute;width:30px;height:2px;background:var(--yellow)}
</style>
</head>
<body>

<!-- Hero -->
<div class="abs hero-bg"></div>
<nav class="nav">
  <a style="left:340px">Home</a>
  <a style="left:442px">About Us</a>
  <a style="left:583px">Services</a>
  <a style="left:703px">Gallery</a>
  <a style="left:827px">Our Team</a>
</nav>
<div class="abs brand">
  <span class="brand-mark"></span>
  <span class="brand-name">Southern Plantskills<br>Academy</span>
</div>
<h1 class="abs hero-title">Empowering<br>Operators,<br>For Progress</h1>
<p class="body-copy" style="left:139px;top:400px;width:340px">Lorem ipsum dolor sit amet, consectetur adipiscing elit,<br>sed do eiusmod tempor incididunt</p>
<div class="btn btn-red" style="left:139px;top:461px;width:136px;height:54px">Learn More</div>
<div class="photo" role="img" aria-label="Excavators loading a dump truck in a rocky quarry" style="left:592px;top:74px;width:572px;height:515px;background:linear-gradient(160deg,#d9d4cc 0%,#bdb3a4 45%,#a58a5a 70%,#9c8e7c 100%)"></div>

<!-- About -->
<div class="photo" role="img" aria-label="Operator in hi-vis vest and hard hat beside a wheel loader" style="left:142px;top:761px;width:365px;height:386px;background:linear-gradient(170deg,#9fb6c9 0%,#8c8a80 45%,#c88a4a 75%,#6f6a61 100%)"></div>
<div class="abs call-box">
  <svg class="abs" style="left:62px;top:58px" width="38" height="38" viewBox="0 0 24 24" fill="none" stroke="#fff" stroke-width="1.3"><path d="M22 16.9v3a2 2 0 0 1-2.2 2 19.8 19.8 0 0 1-8.6-3.1 19.5 19.5 0 0 1-6-6A19.8 19.8 0 0 1 2.1 4.2 2 2 0 0 1 4.1 2h3a2 2 0 0 1 2 1.7c.1.9.4 1.8.7 2.7a2 2 0 0 1-.5 2.1L8 9.8a16 16 0 0 0 6 6l1.3-1.3a2 2 0 0 1 2.1-.4c.9.3 1.8.6 2.7.7a2 2 0 0 1 1.7 2z"/></svg>
  <div class="abs call-label">For Calls:</div>
  <div class="abs call-number">0 800-555-01-42</div>
</div>
<div class="eyebrow" style="left:663px;top:766px">About Us</div>
<h2 class="section-title" style="left:663px;top:792px;font-size:47px">Training Operators<br>for Industry Leaders</h2>
<div class="rule" style="left:663px;top:925px"></div>
<p class="body-copy" style="left:663px;top:955px;width:340px">Lorem ipsum dolor sit amet, consectetur adipiscing elit,<br>sed do eiusmod tempor incididunt ut labore et dolor<br>e magna aliqua. e magna aliqua. e magna</p>
<p class="body-copy" style="left:663px;top:1031px;width:340px">Lorem ipsum dolor sit amet, consectetur adipiscing elit,<br>sed do eiusmod tempor incididunt ut labore et dolor<br>e magna aliqua. e magna aliqua. e magna<br>Lorem ipsum dolor sit amet, consectetur adipiscing elit,<br>sed do eiusmod tempor incididunt ut labore et dolor</p>
<div class="btn btn-yellow" style="left:663px;top:1147px;width:133px;height:51px">Learn More</div>

<!-- Services -->
<div class="abs services-bg"></div>
<div class="eyebrow" style="left:95px;top:1376px">Our Services</div>
<h2 class="section-title" style="left:95px;top:1404px">Services We Provide</h2>
<div class="rule" style="left:95px;top:1489px"></div>
<svg class="abs" style="left:36px;top:1668px" width="44" height="22" viewBox="0 0 44 22" fill="none" stroke="#222" stroke-width="2"><path d="M43 11H3M12 2 3 11l9 9"/></svg>
<svg class="abs" style="left:1124px;top:1668px" width="44" height="22" viewBox="0 0 44 22" fill="none" stroke="#222" stroke-width="2"><path d="M1 11h40M32 2l9 9-9 9"/></svg>
<div class="card" style="left:93px">
  <div class="photo" role="img" aria-label="Site supervisor in front of a yellow excavator" style="background:linear-gradient(160deg,#b7cde0 0%,#8fa2b3 40%,#c4a34a 70%,#3d4350 100%)"></div>
  <div class="card-label">Civil Construction</div>
</div>
<div class="card" style="left:441px">
  <div class="photo" role="img" aria-label="Mine worker in orange hi-vis at sunset" style="background:linear-gradient(150deg,#f2d9a6 0%,#e7b56a 40%,#d9793a 70%,#8a6a4f 100%)"></div>
  <div class="card-label">Mining</div>
</div>
<div class="card" style="left:788px">
  <div class="photo" role="img" aria-label="Excavator working in a sandy quarry" style="background:linear-gradient(150deg,#d9a865 0%,#c78c45 45%,#e0b84a 70%,#a86f34 100%)"></div>
  <div class="card-label">Quarrying</div>
</div>
<div class="btn btn-yellow" style="left:526px;top:1884px;width:133px;height:51px">Learn More</div>

<!-- Video -->
<div class="abs video" role="img" aria-label="Blurred truck driving on a highway at dusk"></div>
<div class="abs play">
  <svg class="abs" style="left:70px;top:55px" width="18" height="20" viewBox="0 0 18 20" fill="none" stroke="#fff" stroke-width="1.5"><path d="M2 2l13 8-13 8z"/></svg>
  <div class="abs play-label">Play Video</div>
</div>
<div class="abs video-title">Explanation Video</div>

<!-- Projects -->
<div class="eyebrow" style="left:95px;top:2530px">Our Services</div>
<h2 class="section-title" style="left:95px;top:2558px">Our Recent Projects</h2>
<div class="rule" style="left:95px;top:2643px"></div>
<div class="photo" role="img" aria-label="Excavator on a muddy residential site" style="left:0;top:2754px;width:144px;height:233px;background:linear-gradient(170deg,#9fb3c4 0%,#6b6b62 50%,#4a4038 100%)"></div>
<div class="photo" role="img" aria-label="Wheel loader at sunrise" style="left:161px;top:2721px;width:274px;height:296px;background:linear-gradient(160deg,#c9d6e2 0%,#e6c98f 40%,#b99c4e 70%,#5d5a53 100%)"></div>
<div class="photo" role="img" aria-label="Smiling operator in hard hat and hi-vis vest" style="left:446px;top:2698px;width:293px;height:342px;background:linear-gradient(170deg,#8aa4c0 0%,#7a8791 40%,#cbc38a 70%,#2f3238 100%)"></div>
<div class="photo" role="img" aria-label="Excavator and dump truck behind an orange safety fence" style="left:761px;top:2721px;width:276px;height:296px;background:linear-gradient(170deg,#4f86c6 0%,#9cb7d1 45%,#c8894a 70%,#9e9a8f 100%)"></div>
<div class="photo" role="img" aria-label="Team of workers in hi-vis on site" style="left:1054px;top:2754px;width:146px;height:233px;background:linear-gradient(170deg,#c7ccd1 0%,#d49a5a 50%,#5a5f6b 100%)"></div>
<div class="btn btn-yellow" style="left:534px;top:3065px;width:119px;height:32px;font-size:12px;font-weight:600;text-transform:none">View All</div>

<!-- Banner -->
<div class="abs banner" role="img" aria-label="Hiraketo excavator on a gravel site, darkened"></div>
<h2 class="abs banner-title">Where Operators<br>Thrive and Industries Flourish</h2>
<p class="body-copy" style="left:152px;top:3441px;width:340px;color:#eee">Lorem ipsum dolor sit amet, consectetur adipiscing elit,<br>sed do eiusmod tempor incididunt ut labore et dolor</p>
<div class="btn btn-yellow" style="left:152px;top:3506px;width:169px;height:51px">Go to Product Page</div>
<div class="abs lower-bg"></div>
<div class="abs quote">
  <p class="abs quote-text">Lorem ipsum dolor sit amet, consectetur ad ipiscing elit, sed do eiusmod tempor incididunt ut labore et dolore magna aliqua. Ut enim ad minim veniam, quis nostrud exercitation ullamco laboris nisi ut aliquip ex ea commodo consequat. Duis aute irure dolor in reprehenderit</p>
  <svg class="abs" style="left:513px;top:99px" width="98" height="67" viewBox="0 0 98 67" fill="var(--navy)"><circle cx="18" cy="18" r="17"/><path d="M30 28c2 18-8 32-24 38l-2-5c12-6 17-16 15-28z"/><circle cx="70" cy="18" r="17"/><path d="M82 28c2 18-8 32-24 38l-2-5c12-6 17-16 15-28z"/></svg>
</div>

<!-- Contact -->
<div class="photo" role="img" aria-label="Two workers in hard hats reviewing a tablet on site" style="left:152px;top:3923px;width:359px;height:422px;background:linear-gradient(165deg,#c9d8e6 0%,#b7b1a2 40%,#2e4268 70%,#3b4560 100%)"></div>
<div class="abs email-box">
  <svg class="abs" style="left:36px;top:38px" width="38" height="32" viewBox="0 0 38 32" fill="none" stroke="var(--yellow)" stroke-width="1.6"><rect x="2" y="6" width="34" height="24"/><path d="M2 6l17 13 17-13"/><path d="M2 30l12-11M36 30 24 19"/></svg>
  <div class="abs" style="left:88px;top:40px;font-size:8px;color:#c8d3e6;text-transform:uppercase">Need to contact us?</div>
  <div class="abs" style="left:88px;top:54px;font-family:'Tinos',serif;font-size:19px">Email Us</div>
</div>
<div class="eyebrow" style="left:610px;top:3888px">Contact With Us</div>
<h2 class="section-title" style="left:610px;top:3916px">Any Questions?<br>Let’s Talk!</h2>
<div class="rule" style="left:610px;top:4047px"></div>
<div class="field" style="left:608px;top:4098px;width:212px;height:51px">My name is</div>
<div class="field" style="left:824px;top:4098px;width:217px;height:51px">My e-mail</div>
<div class="field" style="left:608px;top:4155px;width:433px;height:51px">I am interested in:</div>
<div class="field" style="left:608px;top:4212px;width:433px;height:133px">My message is:</div>
<div class="btn btn-yellow" style="left:896px;top:4364px;width:145px;height:51px">Send a Message</div>

<!-- Footer -->
<footer class="abs footer">
  <div class="f-label" style="left:103px;top:100px">Visit Office:</div>
  <div class="f-value" style="left:103px;top:120px">48 Quarry Rd. Location, 210</div>
  <div class="f-rule" style="left:103px;top:159px"></div>
  <div class="f-label" style="left:103px;top:176px">Write Email:</div>
  <div class="f-value" style="left:103px;top:196px">hello@plantskills.example</div>
  <div class="f-rule" style="left:103px;top:234px"></div>
  <div class="f-label" style="left:103px;top:250px">Make a Call:</div>
  <div class="f-value" style="left:103px;top:270px">0 (800)-555-01-88</div>

  <div class="abs" style="left:433px;top:118px;display:flex;align-items:center;gap:14px">
    <span style="width:56px;height:56px;border-radius:50%;background:var(--yellow)"></span>
    <span style="font-weight:700;font-size:20px;line-height:24px;color:var(--white);text-transform:uppercase;letter-spacing:.5px">Southern Plantskills<br>Academy</span>
  </div>
  <div class="abs" style="left:490px;top:275px;font-size:12px;color:#c9c9d3">Southern Plantskills Academy</div>

  <div class="f-label" style="left:868px;top:126px">Subscribe to our news</div>
  <div class="f-value" style="left:868px;top:150px;line-height:22px">Always Get Our Latets News<br>&amp; Events Newsletter!</div>
  <div class="abs" style="left:868px;top:227px;width:178px;height:40px;background:#3b3c4a;font-size:11px;color:#a9a9b6;padding:13px 0 0 18px">your email</div>
  <div class="abs" style="left:1054px;top:227px;width:44px;height:40px;background:var(--yellow)">
    <svg class="abs" style="left:15px;top:13px" width="14" height="14" viewBox="0 0 14 14" fill="none" stroke="#fff" stroke-width="2.4"><path d="M4 2l5 5-5 5"/></svg>
  </div>
</footer>

</body>
</html>
```